Business is called "Keel Ledger". Accounting and tax services.

I need a flyer for my new business "Keel Ledger". I am an individual accountant working for himself on the Sunshine Coast in Queensland Australia. I would like to see designs that communicate reliability and trust. I believe my point of difference is that I am always available to my clients and I will cap my number of clients to ensure I can service them properly. Accountants in general seem to have a bad reputation for not responding to clients in a timely fashion, whether by email or phone. This is where I intend to differentiate myself. I have included my business card for ideas on colour and for contact information. I have also included some logo's that should go on the flyer. With the RFN logo, the words "Keel Ledger is a RFN Business" needs to be written either above, below or to the right hand side (as per the business card).

Target Market(s)

Small business owners and individuals requiring taxation and financials

Industry/Entity Type

Public Accounting

Font styles to use
Serif

Requirements
Must have
• Supplied logo's, accounting style pictures etc
Services: Small Business Taxation
Company & Trust Tax Returns
Rental Property Returns
Capital Gains Tax
Individual Tax Returns
BAS and IAS lodgements
Nice to have
• Needs to convey a sense of being reliable and responds to clients quickly.
Should not have
• My name

```html
<!DOCTYPE html>
<html lang="en">
<head>
<meta charset="utf-8">
<title>Keel Ledger – Services Flyer</title>
<link href="https://fonts.googleapis.com/css2?family=Playfair+Display:wght@500;700;800&family=Lora:wght@400;500;600&display=swap" rel="stylesheet">
<style>
  :root {
    --green: #27a589;
    --ink: #1f1f22;
    --white: #ffffff;
    --paper: #ffffff;
    --sky: #d3d4dc;
    --partner-blue: #1aa9e4;
    --body-blue: #1f55a8;
    --badge-green: #8cc63f;
    --page-bg: #e9e9ec;
    --display: "Playfair Display", Georgia, serif;
    --text: "Lora", Georgia, serif;
  }
  * { box-sizing: border-box; margin: 0; padding: 0; }
  html, body { width: 885px; height: 1200px; overflow: hidden; background: var(--page-bg); }
  .flyer {
    position: relative;
    width: 885px; height: 1200px;
    background: var(--paper);
    font-family: var(--text);
    color: var(--ink);
    overflow: hidden;
  }
  .flyer__shapes { position: absolute; inset: 0; }

  .brand {
    position: absolute; left: 25px; top: 24px; width: 260px;
    text-align: center;
  }
  .brand__mark {
    width: 84px; height: 84px; margin: 0 auto 14px;
    border: 3px solid var(--ink); border-radius: 50%;
  }
  .brand__name {
    font-family: var(--display);
    font-weight: 500; font-size: 26px; letter-spacing: 6px;
    color: var(--ink); white-space: nowrap;
  }

  .headline {
    position: absolute; left: 43px; top: 396px;
    font-family: var(--display);
    font-size: 56px; line-height: 60px; text-transform: uppercase;
  }
  .headline__accent { display: block; font-weight: 800; color: var(--green); }
  .headline__plain { display: block; font-weight: 500; color: var(--ink); }

  .services { position: absolute; left: 43px; top: 666px; color: var(--white); }
  .services__title {
    font-family: var(--display);
    font-size: 40px; font-weight: 800; letter-spacing: 1px; margin-bottom: 28px;
  }
  .services__list { list-style: none; }
  .service {
    display: flex; align-items: center; height: 77px;
    margin-top: -22px; margin-bottom: 22px;
  }
  .service__icon {
    width: 54px; height: 54px; border: 2.5px solid var(--white); border-radius: 50%;
    display: flex; align-items: center; justify-content: center; flex: none;
  }
  .service__icon svg { width: 30px; height: 30px; }
  .service__label {
    margin-left: 19px; font-size: 16px; line-height: 21px; font-weight: 500;
    text-transform: uppercase; letter-spacing: 0.3px;
  }

  .partner {
    position: absolute; left: 462px; top: 770px;
    width: 132px; height: 132px; border-radius: 50%;
    background: var(--white);
    display: flex; align-items: center; justify-content: center;
  }
  .partner__name { font-size: 34px; font-weight: 600; color: var(--partner-blue); }

  .registration {
    position: absolute; left: 526px; top: 932px; width: 80px; text-align: center;
  }
  .registration__badge {
    width: 70px; height: 70px; margin: 0 auto 4px; border-radius: 50%;
    border: 3px solid var(--ink); background: var(--badge-green);
  }
  .registration__text { font-size: 9px; line-height: 11px; color: var(--ink); }

  .affiliation {
    position: absolute; left: 628px; top: 922px; width: 237px;
  }
  .affiliation__logo {
    height: 88px; display: flex; align-items: center; gap: 18px; padding-left: 20px;
  }
  .affiliation__square { width: 60px; height: 60px; background: var(--body-blue); flex: none; }
  .affiliation__name { font-size: 52px; font-weight: 600; color: var(--body-blue); }
  .affiliation__statement {
    margin-top: 4px; padding-left: 20px;
    font-size: 13px; line-height: 16px; font-weight: 500; color: var(--ink); white-space: nowrap;
  }

  .contact {
    position: absolute; left: 620px; top: 1074px; list-style: none;
    font-size: 17px; line-height: 21px; color: var(--ink);
  }
  .contact__item { display: flex; align-items: center; gap: 12px; }
  .contact__icon { width: 17px; height: 17px; flex: none; }
</style>
</head>
<body>
<main class="flyer">
  <svg class="flyer__shapes" width="885" height="1200" viewBox="0 0 885 1200">
    <defs>
      <linearGradient id="coinTones" x1="0" y1="0" x2="0" y2="1">
        <stop offset="0" stop-color="#d3d4dc"/>
        <stop offset="0.3" stop-color="#c9c8cc"/>
        <stop offset="0.5" stop-color="#8c7d68"/>
        <stop offset="0.75" stop-color="#4a3f34"/>
        <stop offset="1" stop-color="#1f1b18"/>
      </linearGradient>
    </defs>
    <path role="img" aria-label="Photograph of stacked coins against a pale grey background"
          fill="url(#coinTones)"
          d="M390 0 H885 V858 C790 850 660 905 574 891 C520 880 505 850 505 814 C500 740 490 680 471 637 C455 560 430 510 413 482 C370 440 325 420 305 370 C280 320 240 280 262 200 C280 110 330 40 390 0 Z"/>
    <path class="green-panel" fill="var(--green)"
          d="M0 637 C40 625 95 608 150 615 C215 625 265 640 300 690 C335 740 345 780 375 820 C410 870 445 905 470 960 C495 1020 505 1060 503 1100 C500 1140 492 1165 470 1185 C520 1180 580 1165 643 1161 C720 1156 810 1150 885 1156 V1200 H0 Z"/>
  </svg>

  <header class="brand">
    <div class="brand__mark"></div>
    <p class="brand__name">KEEL LEDGER</p>
  </header>

  <h1 class="headline">
    <span class="headline__accent">Available</span>
    <span class="headline__plain">To my</span>
    <span class="headline__accent">Clients</span>
  </h1>

  <section class="services">
    <h2 class="services__title">SERVICES</h2>
    <ul class="services__list">
      <li class="service">
        <span class="service__icon"><svg viewBox="0 0 30 30" fill="none" stroke="#fff" stroke-width="2"><rect x="7" y="4" width="16" height="22" rx="2"/><path d="M11 10h8M11 15h8M11 20h5"/></svg></span>
        <span class="service__label">Small<br>Business Taxation</span>
      </li>
      <li class="service">
        <span class="service__icon"><svg viewBox="0 0 30 30" fill="none" stroke="#fff" stroke-width="2"><rect x="5" y="8" width="20" height="16" rx="2"/><circle cx="15" cy="16" r="4"/><path d="M10 8V5h10v3"/></svg></span>
        <span class="service__label">Company &amp;<br>Trust Tax Returns</span>
      </li>
      <li class="service">
        <span class="service__icon"><svg viewBox="0 0 30 30" fill="none" stroke="#fff" stroke-width="2"><path d="M6 15 15 6l9 9"/><path d="M9 13v11h12V13"/><rect x="13" y="17" width="4" height="7"/></svg></span>
        <span class="service__label">Rental<br>Property Returns</span>
      </li>
      <li class="service">
        <span class="service__icon"><svg viewBox="0 0 30 30" fill="none" stroke="#fff" stroke-width="2"><rect x="9" y="4" width="14" height="20" rx="2"/><path d="M18 9h-3.5a2 2 0 0 0 0 4h2a2 2 0 0 1 0 4H13M16 7v12"/><path d="M5 22l3 3 5-5"/></svg></span>
        <span class="service__label">Capital<br>Gains Tax</span>
      </li>
      <li class="service">
        <span class="service__icon"><svg viewBox="0 0 30 30" fill="none" stroke="#fff" stroke-width="2"><path d="M24 15a9 9 0 1 1-3-6.7"/><path d="M21 4v5h-5"/><path d="M18 11h-3.5a2 2 0 0 0 0 4h1a2 2 0 0 1 0 4H12M15 9v12"/></svg></span>
        <span class="service__label">Individual<br>Tax Returns</span>
      </li>
      <li class="service">
        <span class="service__icon"><svg viewBox="0 0 30 30" fill="none" stroke="#fff" stroke-width="2"><path d="M8 4h10l5 5v17H8z"/><path d="M18 4v5h5M11 13h9M11 17h9M11 21h6"/></svg></span>
        <span class="service__label">BAS and<br>IAS Lodgements</span>
      </li>
    </ul>
  </section>

  <div class="partner"><span class="partner__name">tallyo</span></div>

  <div class="registration">
    <div class="registration__badge"></div>
    <p class="registration__text">Tax agent<br>51827390</p>
  </div>

  <div class="affiliation">
    <div class="affiliation__logo">
      <span class="affiliation__square"></span>
      <span class="affiliation__name">RFN</span>
    </div>
    <p class="affiliation__statement">Keel Ledger is a RFN Business</p>
  </div>

  <ul class="contact">
    <li class="contact__item">
      <svg class="contact__icon" viewBox="0 0 17 17" fill="none" stroke="var(--green)" stroke-width="1.6"><path d="M4 2l3 3-1.5 2a8 8 0 0 0 4.5 4.5L12 10l3 3-2 2C7 15 2 10 2 4z"/></svg>
      <span>0412 555 098</span>
    </li>
    <li class="contact__item">
      <svg class="contact__icon" viewBox="0 0 17 17" fill="none" stroke="var(--green)" stroke-width="1.6"><circle cx="8.5" cy="8.5" r="7"/><path d="M5 6.5h7v5H5zM5 6.5l3.5 2.5 3.5-2.5"/></svg>
      <span>hello@keelledger.com.au</span>
    </li>
    <li class="contact__item">
      <svg class="contact__icon" viewBox="0 0 17 17" fill="none" stroke="var(--green)" stroke-width="1.6"><circle cx="8.5" cy="8.5" r="7"/><ellipse cx="8.5" cy="8.5" rx="3" ry="7"/><path d="M1.5 8.5h14"/></svg>
      <span>www.keelledger.com.au</span>
    </li>
  </ul>
</main>
</body>
</html>
```